Blockchain Analytics Firm Needs Logo And Website Design

We need a logo and a very basic website for a company based in Linköping, Sweden called 'Vextor'. We build custom machine learning and AI solutions for companies based on blockchain. We are not picky about the colors, but the design should communicate modernity and stability.
We like the following websites:
https://www.pallidwren.co.uk/
https://www.tormacapitalhouse.com/
Target Market(s)
Our customers are startups that have their own product based on blockchain or other distributed ledger technology.
Industry/Entity Type
It Company
Contact Information for Business Card
Name, title and email address
Logo Text
Our company name and "Blockchain Analytics"
Font styles to use
Colors
Designer to choose colors to be used in the design.
Requirements
Must have
- The website and logo need to be modern and clean. In the beginning, we will not be filling out all sections of the website (team, clients, etc.) but we will need to have these set up so we can eventually use them.
Nice to have
- We like angular graphics and some animations on the webpage would be nice.

```html
<!DOCTYPE html>
<html lang="en">
<head>
<meta charset="utf-8">
<title>Vextor — Blockchain Analytics</title>
<link href="https://fonts.googleapis.com/css2?family=Lato:wght@400;700&display=swap" rel="stylesheet">
<style>
:root{
  --ink:#262626;
  --dark:#1e1e1e;
  --footer:#1a1a1a;
  --blush:#fdf1f0;
  --red:#e8453c;
  --blue:#3fa0e8;
  --purple:#4a2fd0;
  --violet:#321694;
  --navy:#0a1420;
  --grey:#555;
  --light:#ddd;
  --white:#fff;
}
*{margin:0;padding:0;box-sizing:border-box}
html,body{width:1200px;height:3383px;overflow:hidden}
body{font-family:'Lato',sans-serif;background:var(--white);position:relative;color:var(--grey)}
.abs{position:absolute}
.site-header{left:0;top:0;width:1200px;height:131px;background:var(--ink)}
.brand{left:74px;top:40px;display:flex;align-items:center;gap:14px}
.brand-square{width:40px;height:40px;background:var(--red)}
.brand-name{font-size:34px;font-weight:700;color:var(--red);letter-spacing:1px}
.header-icons{right:74px;top:52px;display:flex;gap:24px}
.panels{left:0;top:131px}
.hero-copy{left:162px;top:276px;width:400px}
.hero-title{font-size:45px;font-weight:700;color:var(--red);line-height:1.1;letter-spacing:1px}
.hero-sub{font-size:32px;color:var(--blue);line-height:1.2}
.hero-text{font-size:20px;color:#333;line-height:1.35;margin-top:10px}
.btn-more{display:inline-block;margin-top:40px;width:153px;height:43px;background:var(--purple);color:var(--white);font-size:12px;font-weight:700;text-align:center;line-height:43px;letter-spacing:.5px}
.video{left:560px;top:221px;width:564px;height:343px;border:6px solid var(--white);box-shadow:0 4px 14px rgba(0,0,0,.35);background:linear-gradient(120deg,#0f0d12 0%,#2a2232 55%,#3e3346 100%)}
.play{left:50%;top:42%;transform:translate(-50%,-50%)}
.about{left:512px;top:926px;width:610px;color:var(--white)}
.about h2{font-size:31px;font-weight:400;line-height:1.25}
.about p{font-size:14px;line-height:27px;margin-top:22px;color:#eee}
.ml{left:74px;top:1340px;width:600px;color:var(--white)}
.ml h2{font-size:31px;font-weight:400}
.ml p{font-size:13.5px;line-height:25px;margin-top:18px}
.ai{right:75px;top:1854px;width:560px;color:var(--white);text-align:right}
.ai h2{font-size:31px;font-weight:400}
.ai p{font-size:13.5px;line-height:25px;margin-top:18px}
.icon-head{left:756px;top:1275px;width:304px;height:270px;border-radius:40px;background:radial-gradient(circle,#1f4f7a 0%,rgba(30,30,30,0) 70%)}
.icon-brain{left:117px;top:1827px;width:221px;height:275px;border-radius:30px;background:radial-gradient(circle,#f5b5b0 0%,rgba(253,241,240,0) 70%)}
.testimonial{left:0;top:2215px;width:1200px;height:334px;background:radial-gradient(ellipse at 60% 80%,#1b3550 0%,var(--navy) 65%);text-align:center}
.avatar{left:550px;top:65px;width:100px;height:100px;border-radius:50%;border:4px solid #c9c9c9;background:linear-gradient(#7a7a7a,#4a4a4a)}
.quote{left:150px;top:184px;width:900px;font-size:13.5px;line-height:25px;color:var(--light)}
.quote-name{left:0;top:261px;width:1200px;font-size:14px;color:var(--blue)}
.blog-title{left:74px;top:2594px;font-size:31px;color:#333;font-weight:400}
.blog-arrows{left:1076px;top:2611px;display:flex;gap:10px}
.card{top:2680px;width:513px}
.card-img{width:513px;height:214px}
.card h3{font-size:20px;color:var(--purple);font-weight:700;margin-top:24px}
.card p{font-size:13.5px;line-height:24px;color:var(--grey);margin-top:6px}
.card-meta{display:flex;justify-content:space-between;margin-top:14px;font-size:13px;color:var(--red)}
.card-meta span{display:flex;align-items:center;gap:8px}
.site-footer{left:0;top:3136px;width:1200px;height:247px;background:var(--footer);color:#9a9a9a;font-size:12.5px;line-height:24px}
.foot-brand{left:74px;top:44px;display:flex;align-items:center;gap:10px}
.foot-brand .brand-square{width:26px;height:26px}
.foot-brand .brand-name{font-size:24px}
.copyright{left:74px;top:112px;font-size:11px;line-height:20px;color:#5d5d5d}
.socials{left:74px;top:176px;display:flex;gap:16px}
.socials i{display:block;width:18px;height:18px;border-radius:50%;background:#6a6a6a}
.foot-col{top:44px}
.foot-col h4{font-size:16px;color:var(--white);font-weight:700;margin-bottom:16px;letter-spacing:.3px}
.hours-row{display:flex;gap:30px}
.email-row{display:flex;margin-top:2px}
.email-row .field{width:192px;height:36px;background:var(--white);color:#888;font-size:11px;line-height:36px;padding-left:10px}
.email-row .go{width:34px;height:36px;background:var(--blue);display:flex;align-items:center;justify-content:center}
</style>
</head>
<body>

<header class="site-header abs">
  <div class="brand abs"><span class="brand-square"></span><span class="brand-name">Vextor</span></div>
  <div class="header-icons abs">
    <svg width="22" height="22" viewBox="0 0 22 22"><circle cx="9" cy="9" r="6.5" fill="none" stroke="#fff" stroke-width="3"/><line x1="14" y1="14" x2="20" y2="20" stroke="#fff" stroke-width="3.5" stroke-linecap="round"/></svg>
    <svg width="22" height="22" viewBox="0 0 22 22"><rect y="3" width="22" height="3" fill="#fff"/><rect y="10" width="22" height="3" fill="#fff"/><rect y="17" width="22" height="3" fill="#fff"/></svg>
  </div>
</header>

<svg class="panels abs" width="1200" height="2084" viewBox="0 58 532 924" preserveAspectRatio="none">
  <rect x="0" y="58" width="532" height="924" fill="#fdf1f0"/>
  <path d="M0,165 L230,355 Q250,372 275,362 L340,262" fill="none" stroke="#e8453c" stroke-width=".6"/>
  <path d="M450,58 Q480,60 500,85 L532,118" fill="none" stroke="#e8453c" stroke-width=".6"/>
  <path d="M215,752 L330,757" fill="none" stroke="#e8453c" stroke-width=".6"/>
  <path d="M470,862 L330,980 M532,910 L430,982" fill="none" stroke="#e8453c" stroke-width=".6"/>
  <rect x="-135" y="-135" width="270" height="270" rx="28" transform="translate(22,395) rotate(45)" fill="#321694"/>
  <rect x="-205" y="-205" width="410" height="410" rx="36" transform="translate(400,530) rotate(45)" fill="#1e1e1e"/>
  <path d="M0,533 L228,533 Q243,533 253,545 L317,630 Q324,642 317,654 L253,740 Q243,752 228,752 L0,752 Z" fill="#e8453c"/>
  <path d="M532,757 L312,757 Q297,757 287,769 L216,858 Q209,866 216,875 L287,963 Q297,975 312,975 L532,975 Z" fill="#3fa0e8"/>
</svg>

<div class="hero-copy abs">
  <h1 class="hero-title">VEXTOR</h1>
  <p class="hero-sub">Blockchain Analytics</p>
  <p class="hero-text">Vivamus lobortis aliquam nulla venenatis porta venenatis tellus malesuada.</p>
  <a class="btn-more">LEARN MORE</a>
</div>

<div class="video abs" role="img" aria-label="Video still of two speakers presenting on a dark stage">
  <svg class="play abs" width="60" height="60" viewBox="0 0 60 60"><circle cx="30" cy="30" r="27" fill="rgba(255,255,255,.25)" stroke="#fff" stroke-width="3"/><path d="M24,18 L42,30 L24,42 Z" fill="#fff"/></svg>
</div>

<section class="about abs">
  <h2>About<br>Vextor Data Analytic</h2>
  <p>Vextor is a data analytics startup that can quickly deploy custom machine learning and AI solutions for companies based on Distributed Ledger Technologies (DLT) such as Blockchains.&nbsp; A massive amount of data is generated from these Smart Contracts, particularly from Internet of Things (IoT) applications.&nbsp; We combine this information with traditional data pipelines and present a complete package to our customer.</p>
</section>

<section class="ml abs">
  <h2>Machine Learning</h2>
  <p>Curabitur tempor risus nec ipsum egestas, pellentesque dapibus est bibendum. Nullam condimentum bibendum nisl, at venenatis tellus malesuada a. Aliquam laoreet orci ligula, in sagittis magna vehicula eu. Integer at nisi at libero posuere viverra quis non turpis.</p>
</section>
<div class="icon-head abs" role="img" aria-label="Line illustration of a head with circuit nodes and a gear"></div>

<div class="icon-brain abs" role="img" aria-label="Line illustration of a brain on a microchip"></div>
<section class="ai abs">
  <h2>AI Solutions</h2>
  <p>Curabitur tempor risus nec ipsum egestas, pellentesque dapibus est bibendum. Nullam condimentum bibendum nisl, at venenatis tellus malesuada a. Aliquam laoreet orci ligula, in sagittis magna vehicula eu. Integer at nisi at libero posuere viverra quis non turpis.</p>
</section>

<section class="testimonial abs">
  <div class="avatar abs" role="img" aria-label="Portrait of the quoted client"></div>
  <p class="quote abs">“ Curabitur tempor risus nec ipsum egestas, pellentesque dapibus est bibendum.&nbsp; condimentum bibendum nisl, at venenatis tellus malesuada a. Aliquam laoreet orci ligula, in sagittis magna vehicula eu. Integer at nisi at libero posuere...”</p>
  <p class="quote-name abs">Name Heading</p>
</section>

<h2 class="blog-title abs">Latest from the blog</h2>
<div class="blog-arrows abs">
  <svg width="18" height="18" viewBox="0 0 18 18"><path d="M11,3 L5,9 L11,15 M5,9 H16" fill="none" stroke="#bbb" stroke-width="2.5"/></svg>
  <svg width="18" height="18" viewBox="0 0 18 18"><path d="M7,3 L13,9 L7,15 M13,9 H2" fill="none" stroke="#3fa0e8" stroke-width="2.5"/></svg>
</div>

<article class="card abs" style="left:74px">
  <div class="card-img" role="img" aria-label="Digital currency coin surrounded by glowing circuit icons" style="background:linear-gradient(135deg,#0c2330 0%,#1a4a52 50%,#3d3a1a 100%)"></div>
  <h3>Curabitur tempor risus nec ipsum egestas</h3>
  <p>Pellentesque dapibus est bibendum&nbsp; condimentum bibendum nisl, at venenatis tellus malesuada a. Aliquam laoreet orci ligula, in sagittis magna vehicula eu. Integer at nisi at libero posuere...</p>
  <div class="card-meta"><span>Continue Reading</span><span><svg width="14" height="12" viewBox="0 0 14 12"><path d="M7,0 C11,0 14,2.5 14,5.5 C14,8.5 11,11 7,11 L3,12 L4,9.5 C1.5,8.5 0,7 0,5.5 C0,2.5 3,0 7,0 Z" fill="#e8453c"/></svg>7 Comments</span></div>
</article>

<article class="card abs" style="left:614px">
  <div class="card-img" role="img" aria-label="Person touching a glowing blockchain interface screen" style="background:linear-gradient(135deg,#0a1d3a 0%,#1f5a8a 55%,#6a8fb0 100%)"></div>
  <h3>Curabitur tempor risus nec ipsum egestas</h3>
  <p>Pellentesque dapibus est bibendum&nbsp; condimentum bibendum nisl, at venenatis tellus malesuada a. Aliquam laoreet orci ligula, in sagittis magna vehicula eu. Integer at nisi at libero posuere...</p>
  <div class="card-meta"><span>Continue Reading</span><span><svg width="14" height="12" viewBox="0 0 14 12"><path d="M7,0 C11,0 14,2.5 14,5.5 C14,8.5 11,11 7,11 L3,12 L4,9.5 C1.5,8.5 0,7 0,5.5 C0,2.5 3,0 7,0 Z" fill="#e8453c"/></svg>7 Comments</span></div>
</article>

<footer class="site-footer abs">
  <div class="foot-brand abs"><span class="brand-square"></span><span class="brand-name">Vextor</span></div>
  <p class="copyright abs">Copyright 2018 Company Name.<br>All Rights Reserved.</p>
  <div class="socials abs"><i></i><i></i><i></i><i></i><i></i></div>

  <div class="foot-col abs" style="left:356px">
    <h4>Address Info</h4>
    <p>Norrvik Science Park,<br>Ekbacksgatan 12, SE-582 14<br>Linköping, SWEDEN</p>
    <p style="margin-top:8px;display:flex;align-items:center;gap:14px"><svg width="14" height="10" viewBox="0 0 14 10"><rect width="14" height="10" fill="#9a9a9a"/><path d="M0,0 L7,6 L14,0" fill="none" stroke="#1a1a1a" stroke-width="1.5"/></svg>info@vextor-mail.com</p>
  </div>

  <div class="foot-col abs" style="left:623px">
    <h4>Hours</h4>
    <p>Mon–Fri: 9:00AM–5:00PM</p>
    <p class="hours-row" style="margin-top:10px"><span>Sat &amp; Sun:</span><span>11:00AM–3:00PM</span></p>
  </div>

  <div class="foot-col abs" style="left:898px">
    <h4>Email Sign Up</h4>
    <div class="email-row"><div class="field">Enter Email Address</div><div class="go"><svg width="10" height="14" viewBox="0 0 10 14"><path d="M2,1 L8,7 L2,13" fill="none" stroke="#fff" stroke-width="2.5"/></svg></div></div>
  </div>
</footer>

</body>
</html>
```